Business card for Luxury Portable Restroom Trailer company

We are a Luxury Portable Restroom Trailer Company Called FALCRIDGE HIRES. Based in Orange County California. We provide portable restroom trailers for events, such as, Weddings, Concerts, Charity events, Sporting events, Tournaments, Corporate events, ect. We rent and Sell the Luxury restrooms. Our colors are white, grey, and Orange. As you will see in the logo we uploaded.
There are 2 people in the company so the names and titles will change for the 3 people but card will remain the same. Here is the information for each Person: Dwight Penner CFO 555 318-0476
next Person: Leon Marchetti VP 555 318-0476
Next Person: Owen Marchetti CEO 555 318-0476
Information to include on the card: Luxury Restroom Trailers Rental and Sales. Weddings, Concerts, Charity, Sporting and Corp. Events.

```html
<!DOCTYPE html>
<html lang="en">
<head>
<meta charset="utf-8">
<title>Falcridge Hires – Business Card</title>
<link href="https://fonts.googleapis.com/css2?family=Montserrat:wght@400;500;700;800&display=swap" rel="stylesheet">
<style>
  :root {
    --orange: #f06a25;
    --charcoal: #4a4b4d;
    --grey-strip: #5a5b5e;
    --white: #ffffff;
    --backdrop: #e6e6e6;
  }
  * { box-sizing: border-box; margin: 0; padding: 0; }
  html, body { width: 1200px; height: 856px; overflow: hidden; }
  body {
    background: var(--backdrop);
    font-family: "Montserrat", sans-serif;
    position: relative;
  }
  .card {
    position: absolute;
    top: 273px;
    width: 540px;
    height: 309px;
    overflow: hidden;
    box-shadow: 0 6px 18px rgba(0,0,0,0.18);
  }
  /* Front */
  .card-front { left: 40px; background: var(--white); }
  .brand-block {
    position: absolute;
    left: 20px; top: 60px;
    width: 220px;
    display: flex; flex-direction: column; align-items: center; gap: 14px;
  }
  .brand-dot {
    width: 60px; height: 60px; border-radius: 50%;
    background: var(--orange);
  }
  .brand-name {
    color: var(--orange);
    font-weight: 800;
    font-size: 24px;
    line-height: 1.15;
    letter-spacing: 1px;
    text-align: center;
  }
  .divider {
    position: absolute;
    left: 255px; top: 28px;
    width: 1.5px; height: 190px;
    background: var(--orange);
  }
  .team {
    position: absolute;
    left: 274px; top: 24px;
    list-style: none;
  }
  .member { margin-bottom: 8px; }
  .member-name {
    font-weight: 800;
    font-size: 17px;
    color: var(--charcoal);
    letter-spacing: 0.3px;
    text-transform: uppercase;
  }
  .member-name .surname { color: var(--orange); }
  .member-title {
    font-size: 12px;
    color: var(--charcoal);
    line-height: 1.3;
  }
  .member-phone {
    display: flex; align-items: center; gap: 6px;
    font-size: 13px;
    color: var(--charcoal);
    font-weight: 500;
  }
  .member-phone svg { width: 13px; height: 13px; fill: var(--orange); }
  .front-bands { position: absolute; left: 0; bottom: 0; width: 540px; height: 90px; }
  .band-caption {
    position: absolute;
    right: 16px; bottom: 30px;
    color: var(--white);
    font-size: 13px;
    font-weight: 500;
    letter-spacing: 0.2px;
    white-space: nowrap;
  }
  /* Back */
  .card-back { left: 620px; background: var(--orange); color: var(--white); }
  .back-frame {
    position: absolute;
    left: 50%; top: 46px;
    transform: translateX(-50%);
    border: 3px solid var(--white);
    padding: 10px 30px;
    text-align: center;
    font-weight: 800;
    font-size: 44px;
    letter-spacing: 2px;
    line-height: 1.1;
    white-space: nowrap;
  }
  .services {
    position: absolute;
    left: 0; right: 0; bottom: 38px;
    text-align: center;
    font-size: 14px;
    line-height: 1.7;
    font-weight: 500;
  }
  .services .bullet { margin: 0 6px; }
</style>
</head>
<body>

<section class="card card-front">
  <div class="brand-block">
    <span class="brand-dot"></span>
    <div class="brand-name">FALCRIDGE<br>HIRES</div>
  </div>

  <div class="divider"></div>

  <ul class="team">
    <li class="member">
      <div class="member-name">Dwight <span class="surname">Penner</span></div>
      <div class="member-title">CFO</div>
      <div class="member-phone"><svg viewBox="0 0 24 24"><path d="M6.6 10.8a15.1 15.1 0 0 0 6.6 6.6l2.2-2.2a1 1 0 0 1 1-.25 11.4 11.4 0 0 0 3.6.57 1 1 0 0 1 1 1V20a1 1 0 0 1-1 1A17 17 0 0 1 3 4a1 1 0 0 1 1-1h3.5a1 1 0 0 1 1 1c0 1.25.2 2.45.57 3.57a1 1 0 0 1-.25 1z"/></svg>555 318-0476</div>
    </li>
    <li class="member">
      <div class="member-name">Leon <span class="surname">Marchetti</span></div>
      <div class="member-title">VP</div>
      <div class="member-phone"><svg viewBox="0 0 24 24"><path d="M6.6 10.8a15.1 15.1 0 0 0 6.6 6.6l2.2-2.2a1 1 0 0 1 1-.25 11.4 11.4 0 0 0 3.6.57 1 1 0 0 1 1 1V20a1 1 0 0 1-1 1A17 17 0 0 1 3 4a1 1 0 0 1 1-1h3.5a1 1 0 0 1 1 1c0 1.25.2 2.45.57 3.57a1 1 0 0 1-.25 1z"/></svg>555 318-0476</div>
    </li>
    <li class="member">
      <div class="member-name">Owen <span class="surname">Marchetti</span></div>
      <div class="member-title">CEO</div>
      <div class="member-phone"><svg viewBox="0 0 24 24"><path d="M6.6 10.8a15.1 15.1 0 0 0 6.6 6.6l2.2-2.2a1 1 0 0 1 1-.25 11.4 11.4 0 0 0 3.6.57 1 1 0 0 1 1 1V20a1 1 0 0 1-1 1A17 17 0 0 1 3 4a1 1 0 0 1 1-1h3.5a1 1 0 0 1 1 1c0 1.25.2 2.45.57 3.57a1 1 0 0 1-.25 1z"/></svg>555 318-0476</div>
    </li>
  </ul>

  <svg class="front-bands" viewBox="0 0 540 90" preserveAspectRatio="none">
    <polygon points="270,76 0,76 0,90 270,90" fill="var(--grey-strip)"/>
    <rect x="0" y="68" width="280" height="3" fill="var(--orange)"/>
    <polygon points="262,18 540,0 540,90 262,90 272,60" fill="var(--orange)"/>
    <polygon points="262,18 272,60 262,90 254,90" fill="var(--grey-strip)"/>
  </svg>
  <div class="band-caption">Luxury Portable Restroom Trailer</div>
</section>

<section class="card card-back">
  <div class="back-frame">FALCRIDGE<br>HIRES</div>
  <p class="services">
    <span class="bullet">●</span>Luxury Restroom Trailers Rental and Sales<br>
    <span class="bullet">●</span>Weddings <span class="bullet">●</span>Concerts <span class="bullet">●</span>Charity <span class="bullet">●</span>Sporting and Corp <span class="bullet">●</span>Events
  </p>
</section>

</body>
</html>
```